Vindgerdi - Start-up company selling electricity

Hello let me tell you about Vindgerdi.

Vindgerdi is start-up company selling electricity in Iceland. The operations of the company consist of making power usage forecasts for our customers, purchasing the electricity wholesale from the energy producers, and selling the electricity to the consumer. We are focused on tech by using optimization and machine learning to minimize electricity prices to our customers. Our marketing strategy is to portray a tech company mindset and to show dedication to driving down the electricity price on the market.

We need your help to make our website pop. Possible concepts to work with are as follows:

- Iceland the land of ice and fire
- Green energy
- Innovation
- Tech and data science

Link to our website: https://prufa.vindgerdi-example.is/
We are open to ideas.
Thank you!

Target Market(s)

Electricity consumers both homes and companies.

Number of Pages Required

1 page

Font styles to use
Serif
Sans Serif

```html
<!DOCTYPE html>
<html lang="is">
<head>
<meta charset="utf-8">
<title>Vindgerdi – Sama rafmagn, bara ódýrara</title>
<link href="https://fonts.googleapis.com/css2?family=Montserrat:wght@400;500;600&family=Vollkorn:wght@600;700&display=swap" rel="stylesheet">
<style>
  :root {
    --brand-red: #a33224;
    --brand-navy: #172e55;
    --ink: #1e1e1e;
    --text: #333333;
    --white: #ffffff;
    --footer-bg: #26262a;
    --footer-text: #e4e4e6;
  }
  * { box-sizing: border-box; margin: 0; padding: 0; }
  html, body { width: 1200px; height: 2721px; overflow: hidden; }
  body { position: relative; background: var(--white); font-family: "Montserrat", Arial, sans-serif; color: var(--text); }

  .site-header { position: absolute; top: 0; left: 0; width: 1200px; height: 73px; background: var(--white); border-bottom: 1px solid #e6e6e6; }
  .brand { position: absolute; left: 90px; top: 18px; display: flex; align-items: center; gap: 12px; }
  .brand-dot { width: 30px; height: 30px; border-radius: 50%; background: var(--brand-navy); }
  .brand-name { font-family: "Vollkorn", Georgia, serif; font-weight: 700; font-size: 34px; color: var(--brand-red); letter-spacing: 0.5px; line-height: 1; }
  .main-nav { position: absolute; top: 26px; right: 90px; display: flex; gap: 40px; font-size: 16px; }
  .main-nav a { color: var(--ink); text-decoration: none; }
  .main-nav a.is-active { color: var(--brand-red); }

  .hero { position: absolute; top: 73px; left: 0; width: 1200px; height: 607px; }
  .hero-media { position: absolute; inset: 0; background: radial-gradient(ellipse at 35% 40%, #2b4a7a 0%, #102444 45%, #050b18 100%); }
  .hero-content { position: absolute; inset: 0; text-align: center; color: var(--white); }
  .hero-title { position: absolute; top: 185px; width: 100%; font-family: "Vollkorn", Georgia, serif; font-weight: 700; font-size: 70px; letter-spacing: 1px; }
  .hero-lead { position: absolute; top: 275px; width: 100%; font-size: 17px; font-weight: 600; line-height: 27px; }
  .hero-cta { position: absolute; top: 350px; left: 507px; width: 186px; height: 55px; border-radius: 28px; background: var(--brand-red); color: var(--white); font-weight: 600; font-size: 17px; line-height: 55px; text-decoration: none; }

  .tagline { position: absolute; top: 768px; width: 1200px; text-align: center; font-family: "Vollkorn", Georgia, serif; font-weight: 700; font-size: 42px; color: var(--ink); letter-spacing: 0.5px; }

  .feature-media { position: absolute; }
  .feature-text { position: absolute; width: 468px; }
  .feature-title { font-family: "Vollkorn", Georgia, serif; font-weight: 700; font-size: 32px; color: var(--ink); margin-bottom: 22px; }
  .feature-body { font-size: 16px; line-height: 29.5px; text-align: justify; }
  .btn-row { display: flex; gap: 8px; margin-top: 30px; }
  .btn { display: block; width: 181px; height: 56px; border-radius: 28px; color: var(--white); text-align: center; line-height: 56px; font-size: 17px; text-decoration: none; }
  .btn--red { background: var(--brand-red); }
  .btn--navy { background: var(--brand-navy); }

  .price-grid { display: flex; gap: 52px; margin-top: 14px; }
  .price-value { font-size: 22px; font-weight: 500; color: var(--ink); line-height: 26px; }
  .price-unit { font-size: 15px; line-height: 22px; }
  .price-note { font-size: 15px; line-height: 26px; }

  .site-footer { position: absolute; top: 2518px; left: 0; width: 1200px; height: 203px; background: var(--footer-bg); color: var(--footer-text); text-align: center; }
  .footer-line { font-size: 17px; line-height: 37px; }
  .footer-line:first-child { margin-top: 54px; }
  .sep { margin: 0 8px; }
  .copyright { font-size: 13px; margin-top: 12px; }
</style>
</head>
<body>
  <header class="site-header">
    <div class="brand"><span class="brand-dot"></span><span class="brand-name">VINDGERDI</span></div>
    <nav class="main-nav">
      <a href="#" class="is-active">Viðskiptaskilmálar</a>
      <a href="#">Spurt &amp; svarað</a>
      <a href="#">Um Vindgerdi</a>
    </nav>
  </header>

  <section class="hero">
    <div class="hero-media" role="img" aria-label="Hand holding a transparent digital tablet with glowing circuit and data graphics"></div>
    <div class="hero-content">
      <h1 class="hero-title">VINDGERDI</h1>
      <p class="hero-lead">Lorem ipsum dolor sit amet, consectetur adipiscing elit, sed do eiusmod tempor incididunt ut labore<br>Ut enim ad minim veniam, quis nostrud exercitation ullamco laboris nisi ut</p>
      <a class="hero-cta" href="#">Get Started</a>
    </div>
  </section>

  <h2 class="tagline">SAMA RAFMAGN ~ BARA ÓDÝRARA!</h2>

  <svg class="feature-media" style="left:626px;top:832px" width="574" height="498" viewBox="0 0 574 498" role="img" aria-label="Hand holding a glowing lightbulb with a globe inside, surrounded by green energy icons">
    <defs><radialGradient id="greenGlow" cx="55%" cy="40%" r="70%"><stop offset="0" stop-color="#c9e86a"/><stop offset="0.5" stop-color="#6aa72e"/><stop offset="1" stop-color="#2f5e1c"/></radialGradient></defs>
    <path d="M0,75 Q0,48 40,44 L574,0 L574,498 L40,456 Q0,452 0,412 Z" fill="url(#greenGlow)"/>
  </svg>
  <div class="feature-text" style="left:91px;top:918px">
    <h3 class="feature-title">Velkomin í viðskipti</h3>
    <p class="feature-body">Lorem ipsum dolor sit amet, consectetur adipiscing elit, sed do eiusmod tempor incididunt ut labore et dolore magna aliqua. Ut enim ad minim veniam, quis nostrud exercitation ullamco laboris nisi ut aliquip ex ea commodo consequat. Duis aute irure dolor in reprehenderit in voluptate velit esse cillum dolore eu fugiat nulla pariatur.</p>
    <div class="btn-row"><a class="btn btn--red" href="#">Fyrirtaeki</a><a class="btn btn--navy" href="#">Heimili</a></div>
  </div>

  <svg class="feature-media" style="left:0;top:1388px" width="558" height="497" viewBox="0 0 558 497" role="img" aria-label="Fingers holding a glowing lightbulb beneath a network of connected data points on blue">
    <defs><radialGradient id="blueGlow" cx="35%" cy="45%" r="75%"><stop offset="0" stop-color="#5a8fc4"/><stop offset="0.5" stop-color="#245a8e"/><stop offset="1" stop-color="#123c66"/></radialGradient></defs>
    <path d="M0,0 L512,44 Q558,48 558,95 L558,412 Q558,450 515,455 L0,497 Z" fill="url(#blueGlow)"/>
  </svg>
  <div class="feature-text" style="left:639px;top:1473px">
    <h3 class="feature-title">Verðskrá</h3>
    <p class="feature-body">Lorem ipsum dolor sit amet, consectetur adipiscing elit, sed do eiusmod tempor incididunt ut labore et dolore magna aliqua.</p>
    <div class="price-grid">
      <div><div class="price-value">6.95</div><div class="price-unit">krónur / kWst</div></div>
      <div><div class="price-value">6.22</div><div class="price-unit">krónur / kWst &nbsp;|&nbsp; rafmagnskynding</div></div>
    </div>
    <p class="price-note">Gerðu verðsamanburð</p>
    <div class="btn-row"><a class="btn btn--red" href="#">Verðvísir</a></div>
  </div>

  <svg class="feature-media" style="left:626px;top:1945px" width="574" height="498" viewBox="0 0 574 498" role="img" aria-label="Hand holding a lightbulb among green hexagon icons for recycling, renewable power and ecology">
    <defs><radialGradient id="ecoGlow" cx="60%" cy="50%" r="70%"><stop offset="0" stop-color="#e4ec9a"/><stop offset="0.45" stop-color="#7fb34a"/><stop offset="1" stop-color="#3c6e2a"/></radialGradient></defs>
    <path d="M0,75 Q0,48 40,44 L574,0 L574,498 L40,456 Q0,452 0,412 Z" fill="url(#ecoGlow)"/>
  </svg>
  <div class="feature-text" style="left:91px;top:2074px">
    <h3 class="feature-title">Framtíðin er spennandi</h3>
    <p class="feature-body">Gerum raforkukerfið snallara saman. Vindgerdi notar gervigreind, gagnavísindi og sjálfvirkni til að lágmarka kostnað og stuðla að okrujöfnuði</p>
    <div class="btn-row"><a class="btn btn--red" href="#">Fyrirtaeki</a></div>
  </div>

  <footer class="site-footer">
    <p class="footer-line">Vindgerdi ehf<span class="sep">|</span>Kennitala: 510101-0190<span class="sep">|</span>Vskm númer: 120456</p>
    <p class="footer-line">Sólvangsvegi 8 170 Seltjarnarnesi<span class="sep">|</span>hallo@vindgerdi-example.is<span class="sep">|</span>555-0199</p>
    <p class="copyright">Copyright © Vindgerdi 2021 Allur réttur áskilin</p>
  </footer>
</body>
</html>
```